Upstart Retirement Planning Firm needs help with business card design

Harborview Nest Advisors, LLC is looking for help with business card design. We give advice on investments, insurance, and other financial matters related to retirement. There are some required disclosures that we will provide but mostly we are looking for a professional, classy business card that reflects the theme we have chosen. We have a logo that is attached but we would like to add a phrase; "Turning Your Earned Income Into Retirement Income"

Doubled sided only so that we can add the required disclosures (needed for our industry) on the back of the card. We will provide the exact words for this in 1-2 days.

Target Market(s)

Retirees and Pre-retirees. Professionals 50+ years old

Industry/Entity Type

Financial Planning

Contact Information for Business Card

We currently have two people who will need separate cards so we'd like to have a template so that we can add names for new cards in the future.

For the first run, please show the following information.

Gregor Pelham, MBA, ChFC®, CLU®
Financial Advisor, Registered Representative
gpelham@harborviewnest.example
Phone: (555) 318-2946
Toll Free Fax: (800) 555-0193

Address is
2187 Meadowlark Ridge Rd.
Suite K418
Virginia Beach, VA 23999

Colors
3277b5

Requirements
Must have
• Logo, contact info, small phase to describe business (in description), required legal disclosures on back of the card as follows (in small font)
• Gregor Pelham is a registered representative of and offers securities through Brightmoor Capital Brokerage Corporation, Member FNQX. Brightmoor Capital Brokerage Corporation is a member of the Brightmoor Capital Alliance which is the marketing name for Brightmoor Holding Corporation and its affiliates.
Nice to have
• Rounded edges, raised letters
Should not have
• any colors that aren't in the logo (other than black for font)

```html
<!DOCTYPE html>
<html lang="en">
<head>
<meta charset="utf-8">
<title>Harborview Nest Advisors – Business Card</title>
<link href="https://fonts.googleapis.com/css2?family=Cinzel:wght@400;500&family=Source+Sans+3:wght@400;600&display=swap" rel="stylesheet">
<style>
  :root{
    --stage:#000000;
    --card:#ffffff;
    --brand-blue:#2f5fa8;
    --brand-grey:#8f8f8f;
    --ink:#1e1e1e;
    --rule:#6e6e6e;
    --faint:#edf1f8;
  }
  html,body{margin:0;padding:0;overflow:hidden;}
  body{width:1200px;height:900px;background:var(--stage);position:relative;
       font-family:"Source Sans 3",Arial,sans-serif;color:var(--ink);}
  .card{position:absolute;top:271px;width:456px;height:281px;background:var(--card);
        border-radius:14px;overflow:hidden;}
  .card--front{left:137px;}
  .card--back{left:626px;}

  /* front */
  .front__brand{position:absolute;left:22px;top:30px;width:250px;text-align:center;}
  .front__brand-name{font-family:"Cinzel",Georgia,serif;font-weight:500;font-size:12.5px;
        letter-spacing:.4px;color:var(--ink);white-space:nowrap;}
  .front__brand-rule{height:1px;background:var(--rule);margin:4px 0 0;}
  .front__mark-area{position:absolute;right:-40px;top:20px;width:260px;height:260px;
        border-radius:50%;background:var(--faint);}
  .person{position:absolute;left:21px;top:97px;}
  .person__name{font-size:17.5px;font-weight:600;color:var(--brand-blue);margin:0;}
  .person__creds{font-size:12px;}
  .person__title{font-size:12.5px;margin-top:1px;}
  .contact{position:absolute;left:23px;top:159px;font-size:12.5px;line-height:20.5px;}
  .contact__row{display:flex;align-items:center;gap:6px;}
  .contact__icon{width:10px;height:10px;fill:var(--brand-blue);}
  .contact__label{color:var(--brand-blue);font-weight:600;}
  .contact__fax{font-size:13px;font-weight:600;}
  .address{position:absolute;left:22px;top:228px;font-size:12.5px;line-height:19px;}

  /* back */
  .back__brand{position:absolute;left:0;right:0;top:96px;text-align:center;}
  .back__brand-name{font-family:"Cinzel",Georgia,serif;font-weight:500;font-size:25px;
        color:var(--brand-blue);letter-spacing:.5px;}
  .back__brand-rule{width:332px;height:1px;background:var(--rule);margin:10px auto 0;}
  .tagline{position:absolute;left:0;right:0;top:214px;text-align:center;
        font-family:"Cinzel",Georgia,serif;font-size:12px;letter-spacing:.3px;}
  .tagline__earned{color:var(--brand-blue);font-weight:500;}
  .tagline__retire{color:var(--brand-grey);}
</style>
</head>
<body>
  <section class="card card--front">
    <div class="front__mark-area" role="img" aria-label="Faint brand decoration area"></div>
    <div class="front__brand">
      <div class="front__brand-name">Harborview Nest Advisors, LLC</div>
      <div class="front__brand-rule"></div>
    </div>
    <div class="person">
      <h1 class="person__name">Gregor Pelham, MBA<span class="person__creds">, ChFC®, CLU®</span></h1>
      <div class="person__title">Financial Advisor, Registered Representative</div>
    </div>
    <div class="contact">
      <div class="contact__row">
        <svg class="contact__icon" viewBox="0 0 10 10" aria-hidden="true"><path d="M2 0.5l1.6 2-1 1.1c.6 1.3 1.5 2.2 2.8 2.8l1.1-1 2 1.6-.9 1.7C4.6 8.8 1.2 5.4.3 1.4z"/></svg>
        <span>(555) 318-2946</span>
      </div>
      <div class="contact__row">
        <svg class="contact__icon" viewBox="0 0 10 10" aria-hidden="true"><path d="M0 2h10v6H0z M0 2l5 3.5L10 2" stroke="#fff" stroke-width=".8"/></svg>
        <span>gpelham@harborviewnest.example</span>
      </div>
      <div class="contact__row">
        <span class="contact__label">Toll Free Fax:</span><span class="contact__fax">(800) 555-0193</span>
      </div>
    </div>
    <address class="address" style="font-style:normal">
      2187 Meadowlark Ridge Rd. Suite<br>K418 Virginia Beach, VA 23999
    </address>
  </section>

  <section class="card card--back">
    <div class="back__brand">
      <div class="back__brand-name">Harborview Nest Advisors</div>
      <div class="back__brand-rule"></div>
    </div>
    <p class="tagline" style="margin:0">
      <span class="tagline__earned">Turning Your Earned Income</span>
      <span class="tagline__retire">Into Retirement Income</span>
    </p>
  </section>
</body>
</html>
```